BRISKEL Need a luxury modern business card designed.

Need a luxury modern business card designed. refer to the uploaded files for the company name and logo in the zip file under source files. i will making my descion on monday. so please send in before then so if we need to edit we will have the time. we have a trade show coming up and im on a deadline for printer.

Target Market(s)

high end clients

Contact Information for Business Card

Company nAme and logo. Tobias Fennick Co-Founder / Project Manager Office # 555-318-7094 Cell # 555-642-1586 BRISKEL.CA Tobias@briskel-example.ca

Font styles to use
Other font styles liked:
• Modern

Requirements
Must have
• Company name and logo, contact info, using the black, gold and white color scheme.

```html
<!DOCTYPE html>
<html lang="en">
<head>
<meta charset="utf-8">
<title>BRISKEL Business Card</title>
<link rel="stylesheet" href="https://fonts.googleapis.com/css2?family=Montserrat:wght@300;400;600&family=Work+Sans:wght@400&display=swap">
<style>
  :root {
    --backdrop: #1b1b1b;
    --card: #1f1f1e;
    --card-sheen: #2a2a29;
    --gold: #a8996a;
    --white: #f4f4f2;
    --grey: #b9b9b6;
  }
  * { box-sizing: border-box; margin: 0; padding: 0; }
  html, body {
    width: 1200px; height: 900px; overflow: hidden;
    background: var(--backdrop);
  }
  .canvas {
    position: relative; width: 1200px; height: 900px;
    display: flex; flex-direction: column; align-items: center; justify-content: center; gap: 48px;
  }
  .card {
    position: relative; width: 640px; height: 366px;
    background: linear-gradient(120deg, var(--card) 0%, var(--card) 55%, var(--card-sheen) 100%);
    border-bottom: 4px solid var(--gold);
    box-shadow: 0 18px 40px rgba(0,0,0,0.55);
  }
  /* Front */
  .card-front { display: flex; flex-direction: column; align-items: center; justify-content: center; }
  .brand-lockup { display: flex; flex-direction: column; align-items: center; }
  .brand-row { display: flex; align-items: center; gap: 22px; }
  .brand-square {
    width: 26px; height: 26px; border: 2px solid var(--gold);
  }
  .brand-name {
    font-family: "Montserrat", sans-serif; font-weight: 300;
    font-size: 52px; line-height: 1; letter-spacing: 0.18em; color: var(--white);
    margin-right: -0.18em;
  }
  .brand-rule { width: 100%; height: 1px; background: var(--grey); opacity: 0.6; margin-top: 12px; }
  .brand-tagline-row { display: flex; align-items: center; gap: 12px; margin-top: 8px; width: 100%; }
  .tagline-line { flex: 1; height: 1px; background: var(--grey); opacity: 0.6; }
  .brand-tagline {
    font-family: "Montserrat", sans-serif; font-weight: 400;
    font-size: 11px; letter-spacing: 0.42em; color: var(--grey);
    margin-right: -0.42em; white-space: nowrap;
  }
  /* Back */
  .card-back { display: flex; align-items: center; justify-content: center; padding: 0 24px 20px; }
  .identity { text-align: right; white-space: nowrap; }
  .person-name {
    font-family: "Montserrat", sans-serif; font-weight: 600;
    font-size: 28px; line-height: 1.15; color: var(--gold); letter-spacing: 0.01em;
  }
  .person-role {
    margin-top: 4px;
    font-family: "Work Sans", sans-serif; font-weight: 400;
    font-size: 14px; color: var(--white); letter-spacing: 0.03em;
  }
  .divider { width: 1px; height: 66px; background: var(--gold); margin: 24px 20px 0 22px; flex: none; }
  .contacts { list-style: none; margin-top: 26px; }
  .contact {
    display: flex; align-items: center; gap: 8px;
    font-family: "Work Sans", sans-serif; font-size: 13.5px; line-height: 20px;
    color: var(--white); letter-spacing: 0.03em; white-space: nowrap;
  }
  .contact-icon { width: 11px; height: 11px; flex: none; }
  .contact-icon path, .contact-icon rect { fill: none; stroke: var(--gold); stroke-width: 1.3; }
  .contact-icon .solid { fill: var(--gold); stroke: none; }
</style>
</head>
<body>
<main class="canvas">
  <section class="card card-front" aria-label="Card front">
    <div class="brand-lockup">
      <div class="brand-row">
        <span class="brand-square" aria-hidden="true"></span>
        <h1 class="brand-name">BRISKEL</h1>
      </div>
      <div class="brand-rule"></div>
      <div class="brand-tagline-row">
        <span class="tagline-line"></span>
        <p class="brand-tagline">LUXURY LANDSCAPES</p>
        <span class="tagline-line"></span>
      </div>
    </div>
  </section>

  <section class="card card-back" aria-label="Card back">
    <div class="identity">
      <h2 class="person-name">Tobias Fennick</h2>
      <p class="person-role">Co-Founder</p>
    </div>
    <div class="divider"></div>
    <ul class="contacts">
      <li class="contact">
        <svg class="contact-icon" viewBox="0 0 12 12" aria-hidden="true"><path class="solid" d="M2.2 0.8l2 0 0.8 2.6-1.3 1c0.6 1.4 1.6 2.4 3 3l1-1.3 2.6 0.8 0 2c0 0.7-0.6 1.3-1.3 1.2C4.7 9.7 2.3 7.3 1 2.1 0.9 1.4 1.5 0.8 2.2 0.8z"/></svg>
        <span>555-318-7094</span>
      </li>
      <li class="contact">
        <svg class="contact-icon" viewBox="0 0 12 12" aria-hidden="true"><rect x="3" y="0.8" width="6" height="10.4" rx="1"/><path d="M5.2 9.4h1.6"/></svg>
        <span>555-642-1586</span>
      </li>
      <li class="contact">
        <svg class="contact-icon" viewBox="0 0 12 12" aria-hidden="true"><rect x="0.8" y="2.4" width="10.4" height="7.2" rx="0.6"/><path d="M1 2.8l5 3.8 5-3.8"/></svg>
        <span>briskel.ca Tobias@briskel-example.ca</span>
      </li>
    </ul>
  </section>
</main>
</body>
</html>
```